SkyvornQ Business Cards and Stationary Design

Need a design for our business cards and stationary. I want to carry on the theme of the logo. I want the business cards to have a design on the back. I would like the business cards and the stationary to carry the same theme, design scheme, and branding

Target Market(s)

Airlines and Maintenance Facilities

Industry/Entity Type

Aviation

Contact Information for Business Card

Name
Position Title
Address: 4827 Trellis Hollow Road, Brenmoor Falls, Westvale, 34951
Office Number
Mobile Number
Email
Website

Font styles to use
Serif
Sans Serif

Colors

Designer to choose colors to be used in the design.

```html
<!DOCTYPE html>
<html lang="en">
<head>
<meta charset="utf-8">
<title>SkyvornQ Business Card</title>
<link rel="stylesheet" href="https://fonts.googleapis.com/css2?family=Open+Sans:wght@400;700;800&display=swap">
<style>
  :root {
    --navy: #0d2f66;
    --blue: #1e7cc8;
    --ink: #4a4f57;
    --paper: #ffffff;
    --backdrop: #e6e3e0;
    --rule: #d9dbde;
  }
  * { margin: 0; padding: 0; box-sizing: border-box; }
  html, body { width: 1200px; height: 997px; overflow: hidden; }
  body {
    background: var(--backdrop);
    font-family: "Open Sans", Arial, sans-serif;
    position: relative;
  }
  .card {
    position: absolute;
    left: 250px;
    width: 700px;
    height: 400px;
    background: var(--paper);
    box-shadow: 0 8px 24px rgba(0,0,0,0.12);
    overflow: hidden;
  }
  .card--front { top: 62px; }
  .card--back { top: 535px; }

  .brand {
    display: flex;
    align-items: center;
    gap: 14px;
    color: var(--navy);
    font-weight: 800;
    letter-spacing: 4px;
    text-transform: uppercase;
  }
  .brand__dot {
    border-radius: 50%;
    background: var(--blue);
  }
  .card--front .brand {
    position: absolute;
    left: 0; width: 350px; top: 0; height: 400px;
    justify-content: center;
    font-size: 34px;
  }
  .card--front .brand__dot { width: 24px; height: 24px; }
  .card--back .brand {
    position: absolute; inset: 0;
    justify-content: center;
    font-size: 44px;
  }
  .card--back .brand__dot { width: 30px; height: 30px; }

  .divider {
    position: absolute;
    left: 350px; top: 30px;
    width: 1px; height: 320px;
    background: var(--rule);
  }
  .details {
    position: absolute;
    left: 385px; top: 55px;
    color: var(--ink);
    font-size: 15px;
    line-height: 22px;
  }
  .details__name {
    color: var(--navy);
    font-weight: 700;
    font-size: 21px;
    line-height: 26px;
    text-transform: uppercase;
  }
  .details__title { margin-bottom: 14px; }
  .contact { list-style: none; }
  .contact li { display: flex; align-items: center; gap: 9px; }
  .contact svg { width: 12px; height: 12px; fill: var(--navy); flex: none; }
  .address { margin-top: 10px; padding-left: 21px; }

  .web-band {
    position: absolute;
    right: 0; bottom: 40px;
    width: 300px; height: 52px;
  }
  .web-band svg { position: absolute; inset: 0; }
  .web-band span {
    position: absolute;
    left: 50px; right: 0; top: 0; bottom: 0;
    display: flex; align-items: center; justify-content: center;
    color: #fff;
    font-size: 15px;
    letter-spacing: 4px;
  }
</style>
</head>
<body>
  <section class="card card--front">
    <div class="brand"><span class="brand__dot"></span>SkyvornQ</div>
    <div class="divider"></div>
    <div class="details">
      <p class="details__name">Dorian Vale</p>
      <p class="details__title">President</p>
      <ul class="contact">
        <li><svg viewBox="0 0 12 12"><path d="M2 1l2 0 1 3-1.5 1a6 6 0 0 0 3.5 3.5L8 7l3 1v2a1 1 0 0 1-1 1A9 9 0 0 1 1 2a1 1 0 0 1 1-1z"/></svg>001 555 0187</li>
        <li><svg viewBox="0 0 12 12"><path d="M3 0h6a1 1 0 0 1 1 1v10a1 1 0 0 1-1 1H3a1 1 0 0 1-1-1V1a1 1 0 0 1 1-1zm0 2v7h6V2z"/></svg>001 555 0143</li>
        <li><svg viewBox="0 0 12 12"><path d="M0 2h12v8H0zM1 3l5 4 5-4z" fill-rule="evenodd"/></svg>info@skyvornq.com</li>
      </ul>
      <p class="address">4827 Trellis Hollow Road,<br>Brenmoor Falls, Westvale, 34951</p>
    </div>
    <div class="web-band">
      <svg viewBox="0 0 300 52" preserveAspectRatio="none"><path d="M300 0V52H0Q8 8 50 2L300 0Z" fill="var(--navy)"/></svg>
      <span>www.skyvornq.com</span>
    </div>
  </section>

  <section class="card card--back">
    <div class="brand"><span class="brand__dot"></span>SkyvornQ</div>
  </section>
</body>
</html>
```